Existing Website Requiring new Pages

I have an existing word press website that was built using elementor.
Website: www.tallowcrestcare.com.au
I require the Vacancies page (https://www.tallowcrestcare.com.au/vacancies/) to be modified to display our new properties along with minor tweaks to how the information is presented.
The vacancies to be displayed are the exactly the same as those that are located on the homepage of QMR website (https://qmr.org.au/)
The new pages that link off the Vacancies tab will require custom design.
There are roughly 8 pages/properties to be incorporated. i wish for the design to be very similar to that displayed in the following link; https://www.polunda.com.au/vacancies/merrylands
Along with this the back end has not been updated for the last 3 years so it also requires some maintenance.
Website is in the disability industry and the custom pages will display information relative to Property Vacancies.
I have attached a ZIP file with some design guides, the information for each of the properties (which will need to be modified to show our business name Tallowcrest Care) and the example of how it is to look based off the Polunda website.
If you guys have any suggestions or ideas on how to make this more presentable or possible i'm open to your ideas.
Target Market(s)
People looking for SDA properties custom built for people with a disability
Industry/Entity Type
Disability
Coding
Coded - Design and coding required
Number of Pages Required
5+ page

```html
<!DOCTYPE html>
<html lang="en">
<head>
<meta charset="utf-8">
<title>Hollowbrook SDA Vacancy – Tallowcrest Care</title>
<link href="https://fonts.googleapis.com/css2?family=Roboto:wght@300;400;500;700&family=Montserrat:wght@300;400;500&display=swap" rel="stylesheet">
<style>
:root{
  --teal:#22d3b4;
  --ink:#3c3c3c;
  --text:#555;
  --muted:#8a8a8a;
  --line:#e4e4e4;
  --dark-band:#555555;
  --sun:#f7c45c;
  --footer-bar:#2a2a2a;
  --accent:#e5497d;
  --social:#1f4e8f;
  --badge:#6b3a8e;
}
*{box-sizing:border-box;margin:0;padding:0}
html,body{width:1200px;height:3248px;overflow:hidden;background:#fff}
body{font-family:"Roboto",sans-serif;color:var(--text);position:relative}
.abs{position:absolute}

/* header */
.site-header{left:0;top:0;width:1200px;height:118px;background:#fff}
.brand{left:136px;top:38px;display:flex;align-items:center;gap:10px}
.brand-dot{width:34px;height:34px;border-radius:50%;background:var(--accent)}
.brand-name{font-family:"Roboto",sans-serif;font-weight:500;font-size:22px;color:var(--accent)}
.main-nav{right:135px;top:50px;display:flex;gap:27px;font-size:11px;font-weight:500;color:var(--ink);letter-spacing:.2px}
.main-nav span svg{vertical-align:middle;margin-left:3px}

/* hero */
.hero{left:0;top:118px;width:1200px;height:590px;background:linear-gradient(180deg,#c9d4dd 0%,#e6d8c0 40%,#8b8f7a 75%,#5d6b4c 100%)}
.thumb-strip{left:136px;top:592px;width:930px;height:230px;background:#fff;box-shadow:0 3px 12px rgba(0,0,0,.15)}
.thumb{top:14px;width:216px;height:201px}
.t1{left:16px;background:linear-gradient(180deg,#9fb3c8,#d8d2c6 55%,#5a5a44)}
.t2{left:244px;background:linear-gradient(180deg,#a9c6df,#d86e5e 35%,#e9ddc7 60%,#6f8b4d)}
.t3{left:473px;background:linear-gradient(180deg,#c3d4e3,#8a5a44 40%,#6e4a3a 70%,#486a36)}
.t4{left:699px;background:linear-gradient(180deg,#b8cde0,#8f8a7a 45%,#b9ad96 65%,#5f8a3d)}
.arrow{top:100px;width:30px;height:30px;border-radius:50%;background:#222;display:flex;align-items:center;justify-content:center}

/* main column */
h1.section-title{font-size:35px;font-weight:700;color:var(--ink);letter-spacing:-.3px}
h2.block-title{font-size:19px;font-weight:700;color:var(--ink);text-transform:uppercase}
.copy{font-size:12.5px;line-height:15px;color:var(--text);width:540px}
.ticks{list-style:none}
.ticks li{font-size:12.5px;color:var(--text);height:24px;display:flex;align-items:center;gap:10px}
.tick{width:13px;height:13px;border-radius:2px;background:var(--teal);display:flex;align-items:center;justify-content:center}

.docs{left:136px;top:1755px;width:503px;height:97px;background:#f0f0f0}
.docs h3{position:absolute;left:19px;top:20px;font-size:19px;font-weight:700;color:var(--ink)}
.docs .file{position:absolute;left:19px;top:56px;display:flex;align-items:center;gap:9px;font-size:12px;color:var(--muted)}
.pdf{width:16px;height:20px;background:#e53935;border-radius:2px}
.btn-download{position:absolute;left:367px;top:44px;width:124px;height:30px;border-radius:15px;background:var(--teal);color:#fff;font-size:12.5px;font-weight:700;display:flex;align-items:center;justify-content:center}

.map{left:136px;top:1935px;width:536px;height:299px;background:linear-gradient(135deg,#eef0ee,#e3e9e0 45%,#eceae4)}

/* enquiry card */
.enquiry{left:750px;top:886px;width:316px;height:540px;background:#fff;box-shadow:0 1px 8px rgba(0,0,0,.18);border-radius:3px}
.enquiry .tag{position:absolute;left:63px;top:34px;width:180px;height:33px;background:var(--teal);color:#fff;font-size:19px;font-weight:700;display:flex;align-items:center;justify-content:center}
.enquiry label{position:absolute;font-size:11px;color:var(--muted)}
.field{position:absolute;height:33px;border:1px solid #cfcfcf;border-radius:3px;background:#fff}
.field.select svg{position:absolute;right:9px;top:12px}
.btn-enquire{position:absolute;left:94px;top:474px;width:135px;height:33px;border-radius:17px;background:#222;color:#fff;font-size:12px;font-weight:700;display:flex;align-items:center;justify-content:center}

/* features */
.features{left:748px;top:1478px;width:318px;height:463px;border:1px solid var(--line);border-top:none}
.features h3{height:41px;background:var(--teal);color:#fff;font-size:19px;font-weight:700;padding-left:17px;display:flex;align-items:center}
.features ul{list-style:none}
.features li{height:60px;border-bottom:1px solid var(--line);display:flex;align-items:center;gap:12px;padding-left:18px;font-size:12.5px;color:var(--ink)}
.features li:last-child{border-bottom:none}
.ficon{width:30px;height:30px;border-radius:50%;background:#333;display:flex;align-items:center;justify-content:center}

.contact-band{left:750px;width:316px;height:72px;display:flex;align-items:center;gap:14px;padding-left:18px;color:#fff;font-weight:700}
.phone-band{top:2010px;background:var(--dark-band);font-size:21px}
.mail-band{top:2092px;background:var(--sun);font-size:16px}
.circle{width:38px;height:38px;border-radius:50%;display:flex;align-items:center;justify-content:center}

/* gallery */
.gallery-title{left:0;top:2288px;width:1200px;text-align:center;font-size:35px;font-weight:700;color:var(--ink)}
.gallery{left:137px;top:2364px;width:928px;display:grid;grid-template-columns:repeat(3,303px);grid-auto-rows:256px;gap:7px 9px}
.g1{background:linear-gradient(180deg,#c6d6e6,#efe6d4 50%,#57704a)}
.g2{background:linear-gradient(180deg,#3b4a3a,#2e3a4a 40%,#c99a5a 70%,#3a5a2e)}
.g3{background:linear-gradient(180deg,#3f7cc7,#dfe4e8 45%,#a86a3c 70%,#6f8a4a)}
.g4{background:linear-gradient(180deg,#e8eef3,#f3f1ec 50%,#4f6a3a)}
.g5{background:linear-gradient(180deg,#6f8a7a,#efe2c9 45%,#c8b090 70%,#7aa8c4)}
.g6{background:linear-gradient(180deg,#2c4f8f,#4a70ad 40%,#e8d0a0 70%,#3a4f6a)}

/* footer */
.foot-brand{left:142px;top:3010px;display:flex;align-items:center;gap:10px}
.foot-contact{left:140px;top:3111px;font-family:"Montserrat",sans-serif;font-size:11.5px;color:#777;line-height:20px}
.foot-contact div{display:flex;align-items:center;gap:9px}
.socials{left:520px;top:2978px;display:flex;flex-direction:column;gap:8px}
.socials span{width:30px;height:30px;border-radius:50%;background:var(--social)}
.socials span.badge{background:var(--badge)}
.foot-col{width:212px;font-family:"Montserrat",sans-serif}
.foot-col h4{font-size:13px;font-weight:500;color:#444;border-left:3px solid #1e73be;padding-left:11px;height:14px;line-height:14px;margin-bottom:11px}
.foot-col a{display:block;font-size:11.5px;color:#8a8a8a;text-decoration:none;line-height:20px;padding:5px 0 4px;border-bottom:1px solid var(--line)}
.bottom-bar{left:0;top:3194px;width:1200px;height:54px;background:var(--footer-bar);color:#bbb;font-family:"Montserrat",sans-serif;font-size:9px;display:flex;align-items:center;justify-content:center}
</style>
</head>
<body>

<header class="abs site-header">
  <div class="abs brand"><span class="brand-dot"></span><span class="brand-name">Tallowcrest Care</span></div>
  <nav class="abs main-nav">
    <span>HOME</span><span>ABOUT US</span>
    <span>WHAT WE DO<svg width="8" height="6" viewBox="0 0 8 6"><path d="M1 1l3 3 3-3" fill="none" stroke="#3c3c3c" stroke-width="1.5"/></svg></span>
    <span>REFERRALS</span><span>FEEDBACK</span><span>CONTACT US</span>
  </nav>
</header>

<div class="abs hero" role="img" aria-label="Modern two-storey accessible home with timber screens at dusk"></div>

<div class="abs thumb-strip">
  <div class="abs thumb t1" role="img" aria-label="Rendered house with lit patio"></div>
  <div class="abs thumb t2" role="img" aria-label="Single-storey house with red roof"></div>
  <div class="abs thumb t3" role="img" aria-label="Brick house with gabled roof"></div>
  <div class="abs thumb t4" role="img" aria-label="Grey family home with lawn"></div>
  <div class="abs arrow" style="left:7px"><svg width="10" height="12" viewBox="0 0 10 12"><path d="M7 1L2 6l5 5" fill="none" stroke="#fff" stroke-width="2.2"/></svg></div>
  <div class="abs arrow" style="left:891px"><svg width="10" height="12" viewBox="0 0 10 12"><path d="M3 1l5 5-5 5" fill="none" stroke="#fff" stroke-width="2.2"/></svg></div>
</div>

<main>
  <h1 class="abs section-title" style="left:136px;top:876px">DESCRIPTION</h1>
  <p class="abs copy" style="left:139px;top:934px">Fully Accessible and High Physical Support apartments in Hollowbrook for NDIS participants looking for Specialist Disability Accommodation (SDA).</p>

  <h2 class="abs block-title" style="left:139px;top:991px">Property Details</h2>
  <p class="abs copy" style="left:139px;top:1033px">Set on 760sqm of land in the Greater Western Sydney suburb of Hollowbrook, this Specialist Disability Accommodation (SDA) is designed as a Fully Accessible (FA) / High Physical Support (HPS) home. The east facing home accommodation availability includes:</p>
  <ul class="abs ticks" style="left:139px;top:1119px"><li><span class="tick"><svg width="9" height="8" viewBox="0 0 9 8"><path d="M1 4l2.5 2.5L8 1" fill="none" stroke="#fff" stroke-width="1.6"/></svg></span>6 x 1 bedroom FA/HPS apartments.</li></ul>

  <h2 class="abs block-title" style="left:139px;top:1172px">Property Features</h2>
  <p class="abs copy" style="left:139px;top:1213px">Located in Greater Western Sydney, QMR's Hollowbrook SDA apartment complex will feature:</p>
  <ul class="abs ticks" style="left:139px;top:1248px">
    <li><span class="tick"><svg width="9" height="8" viewBox="0 0 9 8"><path d="M1 4l2.5 2.5L8 1" fill="none" stroke="#fff" stroke-width="1.6"/></svg></span>Sanctuary garden</li>
    <li><span class="tick"><svg width="9" height="8" viewBox="0 0 9 8"><path d="M1 4l2.5 2.5L8 1" fill="none" stroke="#fff" stroke-width="1.6"/></svg></span>Internal lift</li>
    <li><span class="tick"><svg width="9" height="8" viewBox="0 0 9 8"><path d="M1 4l2.5 2.5L8 1" fill="none" stroke="#fff" stroke-width="1.6"/></svg></span>Vegetable and herb garden</li>
    <li><span class="tick"><svg width="9" height="8" viewBox="0 0 9 8"><path d="M1 4l2.5 2.5L8 1" fill="none" stroke="#fff" stroke-width="1.6"/></svg></span>Open space for relaxation and play</li>
    <li><span class="tick"><svg width="9" height="8" viewBox="0 0 9 8"><path d="M1 4l2.5 2.5L8 1" fill="none" stroke="#fff" stroke-width="1.6"/></svg></span>Communal area for gatherings and shared activities</li>
  </ul>
  <p class="abs copy" style="left:139px;top:1389px">Residents are welcome to use their own Supported Independent Living (SIL) provider.</p>

  <h2 class="abs block-title" style="left:139px;top:1420px">Apartment Features</h2>
  <p class="abs copy" style="left:139px;top:1468px">Each apartment is beautifully appointed with:</p>
  <ul class="abs ticks" style="left:139px;top:1504px">
    <li><span class="tick"><svg width="9" height="8" viewBox="0 0 9 8"><path d="M1 4l2.5 2.5L8 1" fill="none" stroke="#fff" stroke-width="1.6"/></svg></span>5star-rated air conditioning</li>
    <li><span class="tick"><svg width="9" height="8" viewBox="0 0 9 8"><path d="M1 4l2.5 2.5L8 1" fill="none" stroke="#fff" stroke-width="1.6"/></svg></span>Fitted-out kitchen</li>
    <li><span class="tick"><svg width="9" height="8" viewBox="0 0 9 8"><path d="M1 4l2.5 2.5L8 1" fill="none" stroke="#fff" stroke-width="1.6"/></svg></span>Bathroom with accessible facilities</li>
  </ul>

  <h2 class="abs block-title" style="left:139px;top:1616px">About Tallowcrest</h2>
  <p class="abs copy" style="left:139px;top:1664px">Quarry Meadow Residences is a charity with extensive experience in SDA. At our heart is the desire to provide residents with SDA housing that meets their needs, in a place they call home. Our team helps NDIS participants, their families and support providers to navigate the complete SDA pathway. Call us on 1300 482 619 for more information today.</p>

  <section class="abs docs">
    <h3>PROPERTY DOCUMENTS</h3>
    <div class="file"><span class="pdf"></span>Hollowbrook SDA Property brochure</div>
    <div class="btn-download">DOWNLOAD</div>
  </section>

  <h2 class="abs block-title" style="left:139px;top:1887px">Address</h2>
  <div class="abs map" role="img" aria-label="Street map showing the property location in Hollowbrook"></div>
</main>

<aside>
  <form class="abs enquiry">
    <div class="tag">ENQUIRE NOW</div>
    <label style="left:20px;top:96px">First Name</label>
    <label style="left:162px;top:96px">Last Name</label>
    <div class="field" style="left:20px;top:114px;width:133px"></div>
    <div class="field" style="left:162px;top:114px;width:134px"></div>
    <label style="left:20px;top:157px">Email</label>
    <div class="field" style="left:20px;top:175px;width:276px"></div>
    <label style="left:20px;top:219px">Role</label>
    <div class="field select" style="left:20px;top:238px;width:276px"><svg width="10" height="7" viewBox="0 0 10 7"><path d="M1 1l4 4 4-4" fill="none" stroke="#777" stroke-width="1.5"/></svg></div>
    <label style="left:20px;top:282px">State</label>
    <div class="field select" style="left:20px;top:300px;width:276px"><svg width="10" height="7" viewBox="0 0 10 7"><path d="M1 1l4 4 4-4" fill="none" stroke="#777" stroke-width="1.5"/></svg></div>
    <label style="left:20px;top:344px">Post Code</label>
    <div class="field" style="left:20px;top:363px;width:276px"></div>
    <label style="left:20px;top:406px">Phone</label>
    <div class="field" style="left:20px;top:424px;width:276px"></div>
    <div class="btn-enquire">ENQUIRE NOW</div>
  </form>

  <section class="abs features">
    <h3>FEATURES</h3>
    <ul>
      <li><span class="ficon"><svg width="16" height="10" viewBox="0 0 16 10"><rect x="1" y="1" width="14" height="6" rx="1" fill="none" stroke="#fff" stroke-width="1.4"/></svg></span>AIR CONDITIONING</li>
      <li><span class="ficon"><svg width="14" height="14" viewBox="0 0 14 14"><circle cx="7" cy="7" r="5" fill="none" stroke="#fff" stroke-width="1.4"/></svg></span>DRYER</li>
      <li><span class="ficon"><svg width="16" height="12" viewBox="0 0 16 12"><path d="M2 11l2-8M6 11V2M10 11V3M14 11l-2-8" stroke="#fff" stroke-width="1.4"/></svg></span>LAWN</li>
      <li><span class="ficon"><svg width="16" height="12" viewBox="0 0 16 12"><rect x="1" y="1" width="14" height="10" rx="1" fill="none" stroke="#fff" stroke-width="1.4"/><rect x="3" y="3" width="7" height="6" fill="#fff"/></svg></span>MICROWAVE</li>
      <li><span class="ficon"><svg width="10" height="16" viewBox="0 0 10 16"><rect x="1" y="1" width="8" height="14" rx="1" fill="none" stroke="#fff" stroke-width="1.4"/><path d="M1 6h8" stroke="#fff" stroke-width="1.4"/></svg></span>REFRIGERATOR</li>
      <li><span class="ficon"><svg width="14" height="16" viewBox="0 0 14 16"><rect x="1" y="1" width="12" height="14" rx="1" fill="none" stroke="#fff" stroke-width="1.4"/><circle cx="7" cy="9" r="3.5" fill="none" stroke="#fff" stroke-width="1.4"/></svg></span>WASHER</li>
      <li><span class="ficon"><svg width="16" height="12" viewBox="0 0 16 12"><path d="M1 4a10 10 0 0 1 14 0M3.5 6.5a6.5 6.5 0 0 1 9 0M6 9a3 3 0 0 1 4 0" fill="none" stroke="#fff" stroke-width="1.4"/><circle cx="8" cy="11" r="1" fill="#fff"/></svg></span>WIFI</li>
    </ul>
  </section>

  <div class="abs contact-band phone-band">
    <span class="circle" style="background:var(--teal)"><svg width="18" height="18" viewBox="0 0 24 24"><path d="M6.6 10.8a15 15 0 0 0 6.6 6.6l2.2-2.2c.3-.3.7-.4 1-.2 1.1.4 2.3.6 3.6.6.6 0 1 .4 1 1V20c0 .6-.4 1-1 1A17 17 0 0 1 3 4c0-.6.4-1 1-1h3.5c.6 0 1 .4 1 1 0 1.3.2 2.5.6 3.6.1.3 0 .7-.2 1z" fill="#fff"/></svg></span>
    + 1300 555 274
  </div>
  <div class="abs contact-band mail-band">
    <span class="circle" style="background:#fff"><svg width="18" height="14" viewBox="0 0 18 14"><rect x="1" y="1" width="16" height="12" rx="1.5" fill="#555"/><path d="M1.5 2l7.5 6 7.5-6" fill="none" stroke="#fff" stroke-width="1.4"/></svg></span>
    info@tallowcrestcare.com
  </div>
</aside>

<h2 class="abs gallery-title">PROPERTY GALLERY</h2>
<section class="abs gallery">
  <div class="g1" role="img" aria-label="Cream rendered home with gabled roof"></div>
  <div class="g2" role="img" aria-label="Brick house lit at dusk"></div>
  <div class="g3" role="img" aria-label="Contemporary white and timber home"></div>
  <div class="g4" role="img" aria-label="White two-storey home with shutters"></div>
  <div class="g5" role="img" aria-label="Modern home with pool at evening"></div>
  <div class="g6" role="img" aria-label="Modern home lit at night"></div>
</section>

<footer>
  <div class="abs foot-brand"><span class="brand-dot"></span><span class="brand-name">Tallowcrest Care</span></div>
  <div class="abs foot-contact">
    <div><svg width="12" height="10" viewBox="0 0 12 10"><rect x="1" y="1" width="10" height="8" rx="1" fill="none" stroke="var(--accent)" stroke-width="1.2"/><path d="M1 2l5 4 5-4" fill="none" stroke="var(--accent)" stroke-width="1.2"/></svg>Email: info@tallowcrestcare.com.au</div>
    <div><svg width="12" height="12" viewBox="0 0 24 24"><path d="M6.6 10.8a15 15 0 0 0 6.6 6.6l2.2-2.2c.3-.3.7-.4 1-.2 1.1.4 2.3.6 3.6.6.6 0 1 .4 1 1V20c0 .6-.4 1-1 1A17 17 0 0 1 3 4c0-.6.4-1 1-1h3.5c.6 0 1 .4 1 1 0 1.3.2 2.5.6 3.6.1.3 0 .7-.2 1z" fill="var(--accent)"/></svg>Phone: +61 0400 555 318</div>
    <div><svg width="12" height="12" viewBox="0 0 12 12"><circle cx="6" cy="6" r="5" fill="none" stroke="var(--accent)" stroke-width="1.2"/><path d="M6 3v3l2 1.5" fill="none" stroke="var(--accent)" stroke-width="1.2"/></svg>Operating Hours: 9AM To 5PM Monday - Friday</div>
  </div>
  <div class="abs socials"><span class="badge"></span><span></span><span></span><span></span></div>
  <nav class="abs foot-col" style="left:605px;top:2970px">
    <h4>ACCOMMODATION</h4>
    <a>Supported Independent Living (SIL)</a>
    <a>Specialist Disability Accommodation (SDA)</a>
    <a>Short term Accommodation (Respite)</a>
    <a>Vacancies</a>
  </nav>
  <nav class="abs foot-col" style="left:838px;top:2970px">
    <h4>WHAT WE DO</h4>
    <a>In Home Care</a>
    <a>Social &amp; Community Services</a>
    <a>Therapeutic Supports</a>
    <a>Support Coordination</a>
    <a>Home Modifications</a>
  </nav>
  <div class="abs bottom-bar">© Copyright 2021 | Tallowcrest Care | All Rights Reserved.</div>
</footer>

</body>
</html>
```